New Organic Skin Care Line Needs to Design a Product Label

***THE WINNER OF THIS PROJECT WILL MOST LIKELY BECOME THE EXCLUSIVE DESIGNER FOR OUR OTHER PRODUCT LABELS***

We need a label design for a new organic skin care product line called "Maple Dew Gala." This specific product is a 100% pure organic coconut oil. It's used for skin hydration, protection, and makeup removal.

Info to include on front label:

1. Logo: Maple Dew Gala (attached)
2. Product Name: Pure Coconut Oil (emphasize "organic" somewhere)
3. Slogan: Hydrate your skin and hair.
4. Size: 8 FL OZ 236mL

Attached is:

1. The brand logo "Maple Dew Gala" with a white background.
2. An image of the bottle we will use.
3. An image of the bottle with lines to show the size and placement of the label.
4. The brand logo "Maple Dew Gala" with a black background. (photoshop file)

What we need:

A simple mock up of the front side of the label on the bottle. We first want to know what it will look like on the bottle given the size and dimensions.

- We would like one label with a white background (including the logo with a white background).
- We would like a second label with a black background (including the logo with a black background, just need to make the black font white instead of black).

We can get a great idea of what to expect from the front side of the label so we will complete the back side once we identify a winner.
Updates

Apologies, but we are now using a different bottle. The previous one is now discontinued. Please view the two most recent images uploaded. One is an image of the new bottle by itself. The other is an image of that bottle with instructions. Please use your most recent designs on the new bottle. Feel free to make any modifications you see fit to compliment the new bottle shape. Added Friday, March 18, 2016

Reason: We are still working with the label company to finalize the size. Once the size is confirmed we will have to tweak labels based on finalized measurements.

Target Market(s)

Women, 18-70

Industry/Entity Type

Skin Care Product

Font styles to use
Decorative
Script

Requirements
Must have
• -"shabby sheek" and "cute" theme
• -soft organic feel
• -the ingredients are organic, pure, and natural. That should be an essence of the label.

```html
<!DOCTYPE html>
<html lang="en">
<head>
<meta charset="utf-8">
<title>Maple Dew Gala – Organic Pure Coconut Oil Labels</title>
<link rel="stylesheet" href="https://fonts.googleapis.com/css2?family=Cinzel:wght@400;700&family=Delius&display=swap">
<style>
  :root {
    --ink-black: #000000;
    --paper-white: #ffffff;
    --rose-pink: #e0197a;
    --rose-fade-dark: rgba(224, 25, 122, 0.62);
    --rose-fade-light: rgba(224, 25, 122, 0.42);
    --coconut-brown: #7a5535;
    --coconut-flesh: #f1ede4;
    --leaf-green: #4a9434;
  }
  * { margin: 0; padding: 0; box-sizing: border-box; }
  html, body { width: 1200px; height: 1000px; overflow: hidden; background: var(--paper-white); }
  .canvas { position: relative; width: 1200px; height: 1000px; background: var(--paper-white); }

  .backdrop-dark {
    position: absolute; left: 0; top: 487px; width: 600px; height: 513px;
    background: var(--ink-black);
  }

  .label { position: absolute; overflow: hidden; text-align: center; transform-origin: top left; }
  .label--black { width: 372px; height: 450px; background: var(--ink-black); color: var(--paper-white); }
  .label--white { width: 367px; height: 435px; background: var(--paper-white); color: var(--ink-black); box-shadow: inset 0 0 0 1px #eee; }

  .label--black.label--large { left: 103px; top: 515px; }
  .label--white.label--large { left: 723px; top: 527px; }
  .label--black.label--small { left: 212px; top: 160px; transform: scale(0.444); }
  .label--white.label--small { left: 818px; top: 170px; transform: scale(0.42); }

  .rose-frame { position: absolute; inset: 0; }
  .label--black .rose-frame {
    background: radial-gradient(ellipse farthest-side at 50% 50%, transparent 70%, var(--rose-fade-dark) 100%);
  }
  .label--white .rose-frame {
    background: radial-gradient(ellipse farthest-side at 50% 50%, transparent 70%, var(--rose-fade-light) 100%);
  }

  .brand-name {
    position: absolute; left: 0; right: 0;
    font-family: "Cinzel", serif; font-weight: 400;
    font-size: 17px; letter-spacing: 4px; white-space: nowrap;
  }
  .label--black .brand-name { top: 152px; }
  .label--white .brand-name { top: 146px; }

  .coconut-art {
    position: absolute; left: 50%; transform: translateX(-50%);
    border-radius: 40% 45% 35% 35%;
    background: linear-gradient(180deg, var(--coconut-brown) 0%, var(--coconut-flesh) 55%, var(--leaf-green) 100%);
  }
  .label--black .coconut-art { top: 192px; width: 130px; height: 82px; }
  .label--white .coconut-art { top: 188px; width: 128px; height: 80px; }

  .product-name {
    position: absolute; left: 0; right: 0;
    font-family: "Cinzel", serif; line-height: 1.25; font-weight: 400;
  }
  .label--black .product-name { top: 281px; }
  .label--white .product-name { top: 273px; }
  .product-name__organic { display: block; font-weight: 700; font-size: 19px; letter-spacing: 0.5px; }
  .product-name__title { display: block; font-size: 19px; }

  .slogan {
    position: absolute; left: 0; right: 0;
    font-family: "Delius", cursive; font-size: 15px; color: var(--rose-pink);
  }
  .label--black .slogan { top: 350px; }
  .label--white .slogan { top: 339px; }

  .size {
    position: absolute; left: 0; right: 0;
    font-family: "Cinzel", serif; font-size: 10.5px; letter-spacing: 0.3px;
  }
  .label--black .size { top: 378px; }
  .label--white .size { top: 366px; }
</style>
</head>
<body>
<main class="canvas">
  <div class="backdrop-dark"></div>

  <section class="label label--black label--small">
    <div class="rose-frame" role="img" aria-label="Pink line-drawn rose border framing the label"></div>
    <p class="brand-name">Maple Dew Gala</p>
    <div class="coconut-art" role="img" aria-label="Illustration of halved coconuts on green leaves"></div>
    <h2 class="product-name"><span class="product-name__organic">Organic</span><span class="product-name__title">Pure Coconut Oil</span></h2>
    <p class="slogan">Hydrate your skin and hair.</p>
    <p class="size">8 FL OZ 236mL</p>
  </section>

  <section class="label label--white label--small">
    <div class="rose-frame" role="img" aria-label="Pink line-drawn rose border framing the label"></div>
    <p class="brand-name">Maple Dew Gala</p>
    <div class="coconut-art" role="img" aria-label="Illustration of halved coconuts on green leaves"></div>
    <h2 class="product-name"><span class="product-name__organic">Organic</span><span class="product-name__title">Pure Coconut Oil</span></h2>
    <p class="slogan">Hydrate your skin and hair.</p>
    <p class="size">8 FL OZ 236mL</p>
  </section>

  <section class="label label--black label--large">
    <div class="rose-frame" role="img" aria-label="Pink line-drawn rose border framing the label"></div>
    <p class="brand-name">Maple Dew Gala</p>
    <div class="coconut-art" role="img" aria-label="Illustration of halved coconuts on green leaves"></div>
    <h2 class="product-name"><span class="product-name__organic">Organic</span><span class="product-name__title">Pure Coconut Oil</span></h2>
    <p class="slogan">Hydrate your skin and hair.</p>
    <p class="size">8 FL OZ 236mL</p>
  </section>

  <section class="label label--white label--large">
    <div class="rose-frame" role="img" aria-label="Pink line-drawn rose border framing the label"></div>
    <p class="brand-name">Maple Dew Gala</p>
    <div class="coconut-art" role="img" aria-label="Illustration of halved coconuts on green leaves"></div>
    <h2 class="product-name"><span class="product-name__organic">Organic</span><span class="product-name__title">Pure Coconut Oil</span></h2>
    <p class="slogan">Hydrate your skin and hair.</p>
    <p class="size">8 FL OZ 236mL</p>
  </section>
</main>
</body>
</html>
```